Business cards and stationary design

We just completed the design of our new logo and we need to print new business cards and letterhead for our nonprofit. We are looking for a fresh new design that shows off our new logo. On letterhead, we must have a column on the right or left to include our Board of Directors (up to 45 names) (see attachment)

Industry/Entity Type

Non-Profit

Contact Information for Business Card

Standard business card with name, title, Company name, mailing address phone numbers, email address and website. Tagline on back "Bringing the homeless home"

Font styles to use
Sans Serif

Requirements
Must have
• include pertinent information above
• new logo
• fonts compatible with logo
• should use logo colors only
Nice to have
• tag lines

```html
<!DOCTYPE html>
<html lang="en">
<head>
<meta charset="utf-8">
<title>Harbor Haven Center — Business Card</title>
<link rel="stylesheet" href="https://fonts.googleapis.com/css2?family=Courier+Prime:wght@700&family=Lato:wght@400;700&display=swap">
<style>
  :root {
    --backdrop: #3a3431;
    --card: #0e0e0e;
    --gold: #f3b327;
    --teal: #1f8ea8;
    --red: #e3262c;
    --ink: #f2f2f2;
    --rule: #5a5a5a;
  }
  * { box-sizing: border-box; margin: 0; padding: 0; }
  html, body { width: 1200px; height: 900px; overflow: hidden; }
  body {
    background: var(--backdrop);
    font-family: "Lato", Arial, sans-serif;
    position: relative;
  }
  .card {
    position: absolute;
    top: 300px;
    width: 520px;
    height: 298px;
    background: var(--card);
    border-radius: 3px;
    box-shadow: 0 6px 18px rgba(0,0,0,.45);
  }
  .card--front { left: 60px; }
  .card--back  { left: 620px; }

  .front-brand {
    position: absolute;
    left: 26px;
    top: 150px;
    display: flex;
    align-items: center;
    gap: 8px;
  }
  .brand-dot {
    width: 12px; height: 12px;
    border-radius: 50%;
    background: var(--gold);
    flex: none;
  }
  .brand-name {
    font-family: "Lato", Arial, sans-serif;
    font-weight: 700;
    color: var(--teal);
    font-size: 19px;
    line-height: 1.15;
  }

  .divider {
    position: absolute;
    left: 200px;
    top: 40px;
    width: 1px;
    height: 200px;
    background: var(--rule);
  }

  .contact {
    position: absolute;
    left: 218px;
    top: 58px;
    color: var(--ink);
  }
  .contact__name {
    font-family: "Courier Prime", "Courier New", monospace;
    font-weight: 700;
    color: var(--gold);
    font-size: 19px;
    letter-spacing: 2px;
    line-height: 1;
  }
  .contact__title {
    font-size: 15px;
    margin-top: 4px;
    margin-bottom: 10px;
  }
  .contact__line {
    display: flex;
    align-items: center;
    gap: 7px;
    font-size: 15px;
    line-height: 21px;
  }
  .contact__line svg { width: 12px; height: 12px; flex: none; }
  .contact__address {
    font-size: 15px;
    line-height: 20px;
    margin-top: 12px;
  }

  .back-brand {
    position: absolute;
    inset: 0;
    display: flex;
    align-items: center;
    justify-content: center;
    gap: 10px;
  }
  .back-brand .brand-name { font-size: 30px; }
  .back-brand .brand-dot { width: 16px; height: 16px; }
</style>
</head>
<body>
  <section class="card card--front" aria-label="Business card front">
    <div class="front-brand">
      <span class="brand-dot"></span>
      <span class="brand-name">Harbor Haven<br>Center</span>
    </div>
    <div class="divider"></div>
    <div class="contact">
      <p class="contact__name">DANIEL REYES</p>
      <p class="contact__title">Managing Director</p>
      <p class="contact__line">
        <svg viewBox="0 0 12 12" aria-hidden="true"><path fill="var(--gold)" d="M2.2 1h2l1 2.6-1.3 1a6.5 6.5 0 0 0 3.4 3.4l1-1.3L11 7.8v2A1.2 1.2 0 0 1 9.8 11C5 11 1 7 1 2.2A1.2 1.2 0 0 1 2.2 1z"/></svg>
        312 555 0147
      </p>
      <p class="contact__line">
        <svg viewBox="0 0 12 12" aria-hidden="true"><rect x="0.5" y="2" width="11" height="8" rx="1" fill="var(--gold)"/><path d="M1 2.8l5 3.6 5-3.6" stroke="var(--card)" stroke-width="1" fill="none"/></svg>
        hello@harborhaven.org
      </p>
      <p class="contact__line">
        <svg viewBox="0 0 12 12" aria-hidden="true"><circle cx="6" cy="6" r="5.5" fill="var(--gold)"/><path d="M0.5 6h11M6 .5c-2.5 3-2.5 8 0 11M6 .5c2.5 3 2.5 8 0 11" stroke="var(--card)" stroke-width=".8" fill="none"/></svg>
        www.harborhaven.org
      </p>
      <p class="contact__address">218, Maple Grove Lane,<br>Springfield IL,60417</p>
    </div>
  </section>

  <section class="card card--back" aria-label="Business card back">
    <div class="back-brand">
      <span class="brand-dot"></span>
      <span class="brand-name">Harbor Haven Center</span>
    </div>
  </section>
</body>
</html>
```